RW Framewell Inc Business cards

We need business cards using our existing logo but slightly modified. Right now the logo says RW Loadbearing Masonry. We want to keep the RW part of the design, but replace the Structural Concrete portion with "FRAMEWELL". Please see the attached file.
Ideally this would be a blank template so we can add Different Names, titles, and phone numbers later.
On the one side we want only the logo and on the other side the detail. I'm attaching an example for you to see.
Please reach out with any other questions. Our address and other details will be given out once we find a design we like.

Target Market(s)

Construction Industry

```html
<!DOCTYPE html>
<html lang="en">
<head>
<meta charset="utf-8">
<title>RW Framewell Inc Business Cards</title>
<link rel="stylesheet" href="https://fonts.googleapis.com/css2?family=Open+Sans:wght@400;700&family=Questrial&display=swap">
<style>
  :root {
    --bg-dark: #1c1c1c;
    --bg-mid: #3a3a3a;
    --brand-blue: #0f72bd;
    --card-grey: #808184;
    --card-white: #ffffff;
    --text-white: #ffffff;
  }
  * { box-sizing: border-box; margin: 0; padding: 0; }
  html, body {
    width: 1200px; height: 900px; overflow: hidden;
    background: radial-gradient(ellipse at 50% 30%, var(--bg-mid), var(--bg-dark) 75%);
    font-family: "Open Sans", sans-serif;
  }
  .stage { position: relative; width: 1200px; height: 900px; }
  .card {
    position: absolute; left: 250px; width: 700px; height: 400px;
    box-shadow: 0 14px 30px rgba(0,0,0,0.55); overflow: hidden;
  }
  .card-front { top: 30px; background: var(--brand-blue); }
  .card-back { top: 470px; background: var(--card-grey); }

  .wordmark {
    display: flex; align-items: center; gap: 14px;
    color: var(--text-white); font-weight: 700; letter-spacing: 2px;
  }
  .card-front .wordmark {
    position: absolute; left: 0; right: 0; top: 0; bottom: 0;
    justify-content: center; font-size: 44px;
  }
  .wordmark-square { width: 18px; height: 18px; background: var(--text-white); }

  .back-band {
    position: absolute; left: 0; top: 0; width: 100%; height: 118px;
    background: var(--brand-blue);
    display: flex; align-items: center; justify-content: center;
  }
  .back-band .wordmark { font-size: 36px; }

  .holder {
    position: absolute; right: 415px; top: 170px; text-align: right;
    color: var(--text-white);
  }
  .holder-name { font-family: "Questrial", sans-serif; font-size: 34px; letter-spacing: 2px; }
  .holder-title { font-size: 20px; margin-top: -4px; }

  .divider {
    position: absolute; left: 312px; top: 165px; width: 2px; height: 110px;
    background: var(--text-white);
  }

  .contacts {
    position: absolute; left: 340px; top: 165px; list-style: none;
    color: var(--text-white); font-size: 20px; line-height: 28px;
  }
  .contacts li { display: flex; align-items: center; gap: 12px; }
  .contacts svg { width: 18px; height: 18px; flex: none; }

  .address-strip {
    position: absolute; left: 0; top: 318px; width: 100%; height: 46px;
    background: var(--card-white);
    display: flex; align-items: center; justify-content: center;
    color: var(--brand-blue); font-size: 21px;
  }
</style>
</head>
<body>
<main class="stage">
  <section class="card card-front" aria-label="Card front">
    <div class="wordmark"><span class="wordmark-square"></span><span>RW FRAMEWELL</span></div>
  </section>

  <section class="card card-back" aria-label="Card back">
    <header class="back-band">
      <div class="wordmark"><span class="wordmark-square"></span><span>RW FRAMEWELL</span></div>
    </header>

    <div class="holder">
      <p class="holder-name">JOHN&nbsp;&nbsp;SMITH</p>
      <p class="holder-title">Chief Officer</p>
    </div>

    <span class="divider"></span>

    <ul class="contacts">
      <li>
        <svg viewBox="0 0 24 24" fill="#fff"><path d="M6.6 10.8a15 15 0 0 0 6.6 6.6l2.2-2.2a1 1 0 0 1 1-.25 11.4 11.4 0 0 0 3.6.57 1 1 0 0 1 1 1V20a1 1 0 0 1-1 1A17 17 0 0 1 3 4a1 1 0 0 1 1-1h3.5a1 1 0 0 1 1 1c0 1.25.2 2.45.57 3.6a1 1 0 0 1-.25 1z"/></svg>
        <span>+00 8 38 00 00</span>
      </li>
      <li>
        <svg viewBox="0 0 24 24" fill="none" stroke="#fff" stroke-width="2"><rect x="6" y="2" width="12" height="20" rx="2"/><line x1="11" y1="18" x2="13" y2="18"/></svg>
        <span>+00 0 90 00 00</span>
      </li>
      <li>
        <svg viewBox="0 0 24 24" fill="none" stroke="#fff" stroke-width="2"><rect x="2" y="5" width="20" height="14"/><polyline points="2,5 12,13 22,5"/></svg>
        <span>info@rwframewell.com</span>
      </li>
      <li>
        <svg viewBox="0 0 24 24" fill="none" stroke="#fff" stroke-width="2"><circle cx="12" cy="12" r="10"/><ellipse cx="12" cy="12" rx="4" ry="10"/><line x1="2" y1="12" x2="22" y2="12"/></svg>
        <span>www.rwframewell.com</span>
      </li>
    </ul>

    <footer class="address-strip">Your address line here. Country/ State</footer>
  </section>
</main>
</body>
</html>
```